Create a business promotion flyer to leave in customer mailboxes. We are a bulk petroleum supplier, servicing any industry that requires diesel. Base in griffith NSW, servicing griffith area and surrounds.

Business Name - Terra Diesel
Fuel@terradiesel-example.com.au
Owen - 0491 570 362 ohartley@terradiesel-example.com.au
Liam - 0491 570 718 lprosser@terradiesel-example.com.au
Simon - 0491 570 905 skenway@terradiesel-example.com.au
Office 02 5550 1734

Bulk Fuel deliveries.
Oils & lubricants
Local Family owned business

```html
<!DOCTYPE html>
<html lang="en">
<head>
<meta charset="utf-8">
<title>Terra Diesel – Bulk Fuel Flyer</title>
<link rel="stylesheet" href="https://fonts.googleapis.com/css2?family=Poppins:wght@400;500;600;700;800&family=Barlow+Semi+Condensed:wght@700;800&display=swap">
<style>
  :root {
    --red: #ec1c24;
    --dark: #231f20;
    --ink: #231f20;
    --white: #ffffff;
    --backdrop: #58595b;
    --sky: #7f9cc9;
    --concrete: #e4e2df;
  }
  * { box-sizing: border-box; margin: 0; padding: 0; }
  html, body { width: 1051px; height: 1200px; overflow: hidden; }
  body { background: var(--backdrop); font-family: "Poppins", sans-serif; position: relative; }

  .flyer {
    position: absolute; left: 174px; top: 154px;
    width: 703px; height: 909px;
    background: var(--white); overflow: hidden;
  }
  .hero-photo {
    position: absolute; left: 0; top: 0; width: 703px; height: 432px;
    background: linear-gradient(180deg, var(--sky) 0%, #b9c8de 28%, #c8ccd2 48%, #d9d8d6 62%, var(--concrete) 100%);
  }
  .brand {
    position: absolute; left: 57px; top: 70px;
    font-weight: 600; font-size: 36px; color: var(--red); letter-spacing: -0.5px;
    display: flex; align-items: center; gap: 10px;
  }
  .brand-dot { width: 16px; height: 16px; border-radius: 50%; background: var(--red); }
  .service-area {
    position: absolute; left: 510px; top: 0; width: 166px; height: 186px;
    background: var(--red); color: var(--white);
    display: flex; align-items: center; justify-content: center; text-align: center;
    font-size: 16.5px; line-height: 22px; padding-top: 8px;
  }
  .service-area strong { font-weight: 700; }
  .headline {
    position: absolute; left: 57px; top: 454px; top: 300px;
    font-family: "Barlow Semi Condensed", sans-serif; font-weight: 800;
    font-size: 50px; line-height: 48px; color: var(--ink); letter-spacing: -0.3px;
  }
  .headline .accent { color: var(--red); }

  .panel { position: absolute; left: 0; top: 0; }

  .services { position: absolute; left: 0; top: 0; }
  .service { position: absolute; left: 53px; width: 320px; }
  .service-icon {
    position: absolute; left: 0; top: 0; width: 62px; height: 62px; border-radius: 50%;
    background: var(--red); display: flex; align-items: center; justify-content: center;
  }
  .service-title {
    position: absolute; left: 84px; top: -6px; width: 240px;
    color: var(--white); font-weight: 700; font-size: 20.5px; line-height: 26px; text-transform: uppercase;
  }
  .service-text {
    position: absolute; left: 86px; color: var(--white); font-size: 13px; line-height: 15px;
  }

  .contacts { position: absolute; left: 436px; top: 0; }
  .contact-line {
    position: absolute; left: 0; display: flex; align-items: center; gap: 8px;
    color: var(--ink); white-space: nowrap;
  }
  .contact-line svg { width: 12px; height: 12px; flex: none; }
  .contact-name { font-size: 19px; font-weight: 500; }
  .contact-phone { font-size: 19px; font-weight: 600; }
  .contact-email { font-size: 12.2px; font-weight: 400; }

  .footer {
    position: absolute; left: 0; top: 849px; width: 703px; height: 60px;
    background: var(--red); color: var(--white);
    display: flex; align-items: center; padding-left: 67px;
  }
  .footer-lead { font-size: 14.5px; font-weight: 500; }
  .footer-icon {
    width: 26px; height: 26px; border-radius: 50%; background: var(--dark);
    display: flex; align-items: center; justify-content: center; margin: 0 10px 0 11px;
  }
  .footer-email { font-size: 16px; font-weight: 700; }
</style>
</head>
<body>
<main class="flyer">
  <div class="hero-photo" role="img" aria-label="Photo of a white and red double tanker fuel truck parked in front of a large steel warehouse under a blue cloudy sky"></div>

  <div class="brand"><span class="brand-dot"></span>Terra Diesel</div>

  <div class="service-area"><p>Reliable bulk<br>fuel supply<br>across <strong>Griffith</strong><br>and surrounds</p></div>

  <h1 class="headline"><span class="accent">FUEL FOR</span> FARMING,<br>TRANSPORT &amp; INDUSTRY</h1>

  <svg class="panel" width="703" height="849" viewBox="0 0 703 849" aria-hidden="true">
    <polygon points="0,432 368,432 421,620 371,845 0,845" fill="#ec1c24"/>
    <polygon points="0,418 354,418 403,620 352,845 0,845" fill="#231f20"/>
  </svg>

  <section class="services">
    <div class="service" style="top:485px">
      <div class="service-icon">
        <svg width="32" height="32" viewBox="0 0 32 32" fill="none" stroke="#fff" stroke-width="1.4"><rect x="5" y="3" width="16" height="26" rx="1"/><rect x="8" y="6" width="10" height="5"/><path d="M13 15c-2 3-3 4-3 6a3 3 0 0 0 6 0c0-2-1-3-3-6z"/><path d="M21 10l4 3v12a2 2 0 0 1-4 0v-5"/><line x1="3" y1="29" x2="23" y2="29"/></svg>
      </div>
      <h2 class="service-title">Bulk fuel<br>deliveries.</h2>
      <p class="service-text" style="top:58px">Reliable diesel supply<br>for any industry.</p>
    </div>
    <div class="service" style="top:600px">
      <div class="service-icon">
        <svg width="32" height="32" viewBox="0 0 32 32" fill="none" stroke="#fff" stroke-width="1.4"><path d="M9 8h15a2 2 0 0 1 2 2v18H7V11z"/><path d="M4 5l3-3 3 3-3 3z"/><path d="M13 15c-2 3-3 4-3 6a3 3 0 0 0 6 0c0-2-1-3-3-6z"/><rect x="19" y="14" width="4" height="7" rx="2"/><line x1="7" y1="24" x2="26" y2="24"/></svg>
      </div>
      <h2 class="service-title">Oils &amp;<br>lubricants</h2>
      <p class="service-text" style="top:53px">Quality products to keep your<br>equipment performing at its best.</p>
    </div>
    <div class="service" style="top:716px">
      <div class="service-icon">
        <svg width="36" height="30" viewBox="0 0 36 30" fill="none" stroke="#fff" stroke-width="1.5"><circle cx="7" cy="8" r="4"/><circle cx="18" cy="8" r="4"/><circle cx="29" cy="8" r="4"/><path d="M1 20a6 6 0 0 1 10-4"/><path d="M35 20a6 6 0 0 0-10-4"/><path d="M11 27v-3a7 7 0 0 1 14 0v3"/></svg>
      </div>
      <h2 class="service-title" style="width:260px">Local family<br>owned business</h2>
      <p class="service-text" style="top:54px">Proudly supporting our<br>local community.</p>
    </div>
  </section>

  <section class="contacts">
    <div class="contact-line" style="top:475px"><svg viewBox="0 0 12 12"><circle cx="6" cy="3.5" r="2.6" fill="#ec1c24"/><path d="M1 12a5 5 0 0 1 10 0z" fill="#ec1c24"/></svg><span class="contact-name">Owen</span></div>
    <div class="contact-line" style="top:497px"><svg viewBox="0 0 12 12"><path d="M4 1L2.5 2C1.5 5 3.5 10 7 11l1.5-1L7 8 5.5 8.5C4.5 7 4 5.5 4.3 4L5.5 3z" fill="#ec1c24"/></svg><span class="contact-phone">0491 570 362</span></div>
    <div class="contact-line" style="top:523px"><svg viewBox="0 0 12 12"><rect x="1" y="3" width="10" height="7" fill="#ec1c24"/><path d="M1 3l5 4 5-4" stroke="#fff" fill="none"/></svg><span class="contact-email">ohartley@terradiesel-example.com.au</span></div>

    <div class="contact-line" style="top:570px"><svg viewBox="0 0 12 12"><circle cx="6" cy="3.5" r="2.6" fill="#ec1c24"/><path d="M1 12a5 5 0 0 1 10 0z" fill="#ec1c24"/></svg><span class="contact-name">Liam</span></div>
    <div class="contact-line" style="top:592px"><svg viewBox="0 0 12 12"><path d="M4 1L2.5 2C1.5 5 3.5 10 7 11l1.5-1L7 8 5.5 8.5C4.5 7 4 5.5 4.3 4L5.5 3z" fill="#ec1c24"/></svg><span class="contact-phone">0491 570 718</span></div>
    <div class="contact-line" style="top:617px"><svg viewBox="0 0 12 12"><rect x="1" y="3" width="10" height="7" fill="#ec1c24"/><path d="M1 3l5 4 5-4" stroke="#fff" fill="none"/></svg><span class="contact-email">lprosser@terradiesel-example.com.au</span></div>

    <div class="contact-line" style="top:665px"><svg viewBox="0 0 12 12"><circle cx="6" cy="3.5" r="2.6" fill="#ec1c24"/><path d="M1 12a5 5 0 0 1 10 0z" fill="#ec1c24"/></svg><span class="contact-name">Simon</span></div>
    <div class="contact-line" style="top:687px"><svg viewBox="0 0 12 12"><path d="M4 1L2.5 2C1.5 5 3.5 10 7 11l1.5-1L7 8 5.5 8.5C4.5 7 4 5.5 4.3 4L5.5 3z" fill="#ec1c24"/></svg><span class="contact-phone">0491 570 905</span></div>
    <div class="contact-line" style="top:714px"><svg viewBox="0 0 12 12"><rect x="1" y="3" width="10" height="7" fill="#ec1c24"/><path d="M1 3l5 4 5-4" stroke="#fff" fill="none"/></svg><span class="contact-email">skenway@terradiesel-example.com.au</span></div>

    <div class="contact-line" style="top:761px"><svg viewBox="0 0 12 12" fill="none" stroke="#ec1c24" stroke-width="0.9"><rect x="1" y="5" width="5" height="6"/><rect x="6" y="1" width="5" height="10"/><line x1="7.5" y1="3" x2="9.5" y2="3"/><line x1="7.5" y1="5.5" x2="9.5" y2="5.5"/><line x1="2.5" y1="7.5" x2="4.5" y2="7.5"/></svg><span class="contact-name">Office</span></div>
    <div class="contact-line" style="top:785px"><svg viewBox="0 0 12 12"><path d="M4 1L2.5 2C1.5 5 3.5 10 7 11l1.5-1L7 8 5.5 8.5C4.5 7 4 5.5 4.3 4L5.5 3z" fill="#ec1c24"/></svg><span class="contact-phone">02 5550 1734</span></div>
  </section>

  <footer class="footer">
    <span class="footer-lead">Have questions? Email us at:</span>
    <span class="footer-icon"><svg width="13" height="10" viewBox="0 0 13 10"><rect x="0.5" y="0.5" width="12" height="9" fill="#fff"/><path d="M0.5 0.5l6 5 6-5" stroke="#231f20" fill="none"/></svg></span>
    <span class="footer-email">Fuel@terradiesel-example.com.au</span>
  </footer>
</main>
</body>
</html>
```